Business Card Design

We are a manufacturing and distribution company with most of our customer base being supermarkets. We have established brand guidelines that are attached.

```html
<!DOCTYPE html>
<html lang="en">
<head>
<meta charset="utf-8">
<title>Valmore Business Card</title>
<link rel="stylesheet" href="https://fonts.googleapis.com/css2?family=Roboto:wght@400;500;700;900&display=swap">
<style>
  :root {
    --backdrop: #2d2d2d;
    --card-dark: #262626;
    --card-dark-edge: #1f1f1f;
    --card-light: #ffffff;
    --ink: #222222;
    --ink-soft: #3a3a3a;
    --brand-red: #ef2b35;
    --brand-blue: #0aa3e6;
    --text-light: #f2f2f2;
  }
  * { margin: 0; padding: 0; box-sizing: border-box; }
  html, body {
    width: 1200px;
    height: 960px;
    overflow: hidden;
    background: var(--backdrop);
    font-family: "Roboto", Arial, sans-serif;
  }
  .card {
    position: absolute;
    left: 329px;
    width: 543px;
    height: 310px;
    overflow: hidden;
  }
  .card--front {
    top: 141px;
    background: linear-gradient(135deg, var(--card-dark-edge) 0%, var(--card-dark) 60%, #2a2a2a 100%);
  }
  .card--back {
    top: 508px;
    background: var(--card-light);
  }
  .front-wordmark {
    position: absolute;
    right: 32px;
    top: 246px;
    font-size: 37px;
    font-weight: 900;
    letter-spacing: 2px;
    line-height: 1;
    color: var(--text-light);
  }
  .back-wordmark {
    position: absolute;
    left: 23px;
    top: 92px;
    font-size: 37px;
    font-weight: 900;
    letter-spacing: 5px;
    line-height: 1;
    color: var(--ink);
  }
  .accent-band {
    position: absolute;
    left: 0;
    top: 150px;
    width: 543px;
    height: 12px;
    background: linear-gradient(90deg, var(--brand-red) 0%, #f47a62 40%, var(--brand-blue) 75%, #0a8fdc 100%);
  }
  .contact-panel {
    position: absolute;
    left: 0;
    top: 162px;
    width: 543px;
    height: 148px;
    background: var(--card-dark);
  }
  .person {
    position: absolute;
    right: 26px;
    top: 48px;
    text-align: right;
  }
  .person__name {
    font-size: 24px;
    font-weight: 500;
    letter-spacing: 0.5px;
    line-height: 1;
  }
  .person__first { color: var(--brand-red); }
  .person__last { color: var(--brand-blue); }
  .person__role {
    margin-top: 5px;
    font-size: 12.5px;
    color: var(--ink-soft);
  }
  .address {
    position: absolute;
    right: 26px;
    top: 180px;
    text-align: right;
    font-size: 12.5px;
    line-height: 16px;
    color: var(--text-light);
  }
  .contact-list {
    position: absolute;
    right: 24px;
    top: 224px;
    list-style: none;
    text-align: right;
  }
  .contact-list li {
    display: flex;
    justify-content: flex-end;
    align-items: center;
    gap: 6px;
    height: 19.5px;
    font-size: 12.5px;
    color: var(--text-light);
  }
  .contact-list svg { width: 11px; height: 11px; flex: none; }
</style>
</head>
<body>

<section class="card card--front" aria-label="Card front">
  <div class="front-wordmark">VALMORE</div>
</section>

<section class="card card--back" aria-label="Card back">
  <div class="accent-band" role="img" aria-label="Red and blue decorative wave band"></div>
  <div class="contact-panel"></div>

  <div class="back-wordmark">VALMORE</div>

  <div class="person">
    <div class="person__name"><span class="person__first">DANIEL</span> <span class="person__last">MORROW</span></div>
    <div class="person__role">CEO/Founder</div>
  </div>

  <div class="address">
    2260 Kestrel Lane<br>
    Fairmont Vale, CD 40312
  </div>

  <ul class="contact-list">
    <li>555-208-4417
      <svg viewBox="0 0 12 12" aria-hidden="true"><path d="M2.5 1 L4.5 1 L5.3 3.4 L4 4.4 C4.6 5.8 6.2 7.4 7.6 8 L8.6 6.7 L11 7.5 L11 9.5 C11 10.3 10.3 11 9.5 11 C5 10.7 1.3 7 1 2.5 C1 1.7 1.7 1 2.5 1 Z" fill="var(--brand-red)"/></svg>
    </li>
    <li>hello@valmore.com.au
      <svg viewBox="0 0 12 12" aria-hidden="true"><rect x="0.5" y="2" width="11" height="8" fill="var(--brand-red)"/><path d="M0.8 2.4 L6 6.6 L11.2 2.4" stroke="#fff" stroke-width="1" fill="none"/></svg>
    </li>
    <li>www.valmore.com.au
      <svg viewBox="0 0 12 12" aria-hidden="true"><circle cx="6" cy="6" r="5.3" fill="var(--brand-red)"/><ellipse cx="6" cy="6" rx="2.2" ry="5.3" stroke="#fff" stroke-width="0.8" fill="none"/><path d="M0.8 6 H11.2" stroke="#fff" stroke-width="0.8"/></svg>
    </li>
  </ul>
</section>

</body>
</html>
```